Velvet Pressings Techno Label Business Card

I'm looking for a very clean business card for my Velvet Pressings music label. The label focusses on techno music. The card should include:

• my name : Tomas Brandt as "Founder & CEO"
• email address: tomas@velvet-pressings.example
• web: www.velvet-pressings.example
• facebook logo + /velvetpress
• twitter logo + /velvetpress
• soundcloud logo + /velvetpressings

Feel free to include your ideas! I'm looking forward to discuss about it.

Tomas

Industry/Entity Type

Business

Contact Information for Business Card

I don't like glossy cards. Prefer matt.

Requirements
Nice to have
• Maybe on one side the complete logo, other side just the icon.
Should not have
• Flashy stuff. Must be clean and business like style.

```html
<!DOCTYPE html>
<html lang="en">
<head>
<meta charset="utf-8">
<title>Velvet Pressings – Business Card</title>
<link href="https://fonts.googleapis.com/css2?family=Open+Sans:wght@400;600;700&display=swap" rel="stylesheet">
<style>
  :root {
    --stage: #e9e9e9;
    --label-orange: #f26f1e;
    --card-white: #fbfbfb;
    --ink-black: #1c1c1c;
    --text-grey: #6b6b6b;
    --icon-orange: #ee6b1c;
  }
  * { box-sizing: border-box; margin: 0; padding: 0; }
  html, body {
    width: 1200px;
    height: 726px;
    overflow: hidden;
    background: var(--stage);
    font-family: "Open Sans", Arial, sans-serif;
  }
  .canvas {
    position: relative;
    width: 1200px;
    height: 726px;
  }
  .card {
    position: absolute;
    top: 214px;
    width: 520px;
    height: 298px;
    border-radius: 2px;
  }
  .card--front {
    left: 50px;
    background: var(--label-orange);
    display: flex;
    align-items: center;
    justify-content: center;
    gap: 16px;
  }
  .card--back {
    left: 630px;
    background: var(--card-white);
  }
  .wordmark-dot {
    width: 40px;
    height: 40px;
    border-radius: 50%;
    background: var(--ink-black);
    flex: none;
  }
  .wordmark {
    font-weight: 700;
    font-size: 40px;
    letter-spacing: -0.5px;
    color: var(--ink-black);
  }
  .back-brand {
    position: absolute;
    left: 34px;
    top: 120px;
    display: flex;
    align-items: center;
    gap: 10px;
  }
  .back-brand .wordmark-dot {
    width: 26px;
    height: 26px;
    background: var(--label-orange);
  }
  .back-brand .wordmark {
    font-size: 21px;
    color: var(--label-orange);
    letter-spacing: 0;
  }
  .contact {
    position: absolute;
    left: 268px;
    top: 46px;
  }
  .contact__name {
    font-size: 17px;
    font-weight: 400;
    color: var(--label-orange);
    line-height: 1.2;
  }
  .contact__role {
    font-size: 10.5px;
    color: var(--text-grey);
    margin-top: 2px;
  }
  .contact__list {
    list-style: none;
    margin-top: 46px;
  }
  .contact__item {
    display: flex;
    align-items: center;
    gap: 9px;
    font-size: 11.5px;
    color: var(--text-grey);
    line-height: 19px;
  }
  .contact__icon {
    width: 10px;
    height: 10px;
    flex: none;
  }
  .contact__icon--plain {
    background: var(--icon-orange);
    border-radius: 2px;
  }
</style>
</head>
<body>
<main class="canvas">
  <section class="card card--front" aria-label="Card front">
    <span class="wordmark-dot" aria-hidden="true"></span>
    <span class="wordmark">Velvet Pressings</span>
  </section>

  <section class="card card--back" aria-label="Card back">
    <div class="back-brand">
      <span class="wordmark-dot" aria-hidden="true"></span>
      <span class="wordmark">Velvet Pressings</span>
    </div>

    <div class="contact">
      <h1 class="contact__name">Tomas Brandt</h1>
      <p class="contact__role">Founder &amp; CEO</p>
      <ul class="contact__list">
        <li class="contact__item">
          <svg class="contact__icon" viewBox="0 0 10 10" aria-hidden="true">
            <rect x="0.5" y="1.5" width="9" height="7" fill="var(--icon-orange)"/>
            <path d="M0.5 1.5 L5 5.5 L9.5 1.5" fill="none" stroke="#fff" stroke-width="1"/>
          </svg>
          tomas@velvet-pressings.example
        </li>
        <li class="contact__item">
          <svg class="contact__icon" viewBox="0 0 10 10" aria-hidden="true">
            <circle cx="5" cy="5" r="4.5" fill="var(--icon-orange)"/>
            <path d="M0.5 5 H9.5 M5 0.5 C2.5 3 2.5 7 5 9.5 M5 0.5 C7.5 3 7.5 7 5 9.5" fill="none" stroke="#fff" stroke-width="0.8"/>
          </svg>
          www.velvet-pressings.example
        </li>
        <li class="contact__item">
          <span class="contact__icon contact__icon--plain" aria-hidden="true"></span>
          /velvetpress
        </li>
        <li class="contact__item">
          <span class="contact__icon contact__icon--plain" aria-hidden="true"></span>
          /velvetpress
        </li>
        <li class="contact__item">
          <span class="contact__icon contact__icon--plain" aria-hidden="true"></span>
          /velvetpressings
        </li>
      </ul>
    </div>
  </section>
</main>
</body>
</html>
```